Captivating packaging design for sports company.

We need a packaging design that encompasses our resistance bands workout set. Our focus is quality, convenience, and versatility. The design should be tailored to our broad array of customer across all paths. We would like the packaging to reflect our brand and product features such as: the LBS(weight) listed on each of the bands, convenience for travel and at home, highest quality, for all fitness levels, and free eBook. We'd also like to include a couple of our reviews on the packaging. Please refer to our listing on Varlo for additional information https://www.shopvarlo.com/Brisklane-Athletics-Resistance-Workout-Carrying/dp/K47TR2XMNQ/ref=sr_1_1?ie=UTF8&qid=1470453588&sr=8-1&keywords=brisklane+athletics+resistance+bands
Please reach out with additional questions for any further details. Thank you.
Target Market(s)
Sports, fitness, and health enthusiasts of all ages.
Industry/Entity Type
It Company
Look and feel
Each slider illustrates characteristics of the customer's brand and the style your logo design should communicate.

```html
<!DOCTYPE html>
<html lang="en">
<head>
<meta charset="utf-8">
<title>Brisklane Athletics – Resistance Band Packaging</title>
<link rel="stylesheet" href="https://fonts.googleapis.com/css2?family=Raleway:ital,wght@0,300;0,400;0,700;1,300&display=swap">
<style>
  :root {
    --stage: #e4e4e4;
    --panel: #ffffff;
    --maroon: #7a1a22;
    --maroon-deep: #5c0f16;
    --ink: #1c1c1c;
    --grey-text: #6d6d6d;
    --soft-grey: #cfcfcf;
  }
  * { margin: 0; padding: 0; box-sizing: border-box; }
  html, body { width: 1200px; height: 900px; overflow: hidden; }
  body {
    background: var(--stage);
    font-family: "Raleway", sans-serif;
    position: relative;
  }
  .panel {
    position: absolute;
    background: var(--panel);
    overflow: hidden;
    box-shadow: 0 2px 10px rgba(0,0,0,0.12);
  }
  .panel svg { position: absolute; inset: 0; }

  /* Lid */
  .lid { left: 100px; top: 60px; width: 1000px; height: 420px; }
  .lid .runner-art {
    position: absolute; left: 70px; top: 40px; width: 330px; height: 190px;
  }
  .lid .brand {
    position: absolute; left: 420px; top: 44px;
    display: flex; align-items: center; gap: 10px;
  }
  .lid .title-band-text {
    position: absolute; left: 690px; top: 100px; color: #fff;
    transform: rotate(12deg); transform-origin: left top;
  }
  .lid .title-band-text h2 { font-weight: 700; font-size: 30px; letter-spacing: 0.5px; }
  .lid .title-band-text p { font-weight: 300; font-size: 14px; margin-top: 6px; color: #d8d8d8; }

  /* Front */
  .front { left: 100px; top: 510px; width: 520px; height: 300px; }
  .front .brand {
    position: absolute; left: 70px; top: 115px;
    display: flex; align-items: center; gap: 16px;
  }

  /* Side */
  .side { left: 640px; top: 510px; width: 460px; height: 300px; }
  .side .product-title {
    position: absolute; left: 30px; top: 110px; color: #fff;
  }
  .side .product-title h1 { font-weight: 700; font-size: 26px; white-space: nowrap; }
  .side .product-title p { font-weight: 300; font-size: 14px; line-height: 1.3; margin-top: 4px; color: #e9c9cc; }
  .side .tagline {
    position: absolute; left: 262px; top: 192px; width: 105px;
    font-style: italic; font-weight: 300; font-size: 13px; line-height: 1.3;
    color: var(--grey-text);
  }
  .side .athlete-art {
    position: absolute; right: 15px; top: 30px; width: 70px; height: 220px;
  }

  .brand-mark {
    width: 30px; height: 30px; border-radius: 50%;
    background: var(--maroon);
    flex: none;
  }
  .brand-name {
    font-weight: 700; color: var(--maroon);
    letter-spacing: 1px; text-transform: uppercase; line-height: 1.05;
  }
  .lid .brand-name { font-size: 17px; }
  .front .brand-mark { width: 52px; height: 52px; }
  .front .brand-name { font-size: 30px; }
</style>
</head>
<body>

  <section class="panel lid" aria-label="Box lid">
    <svg width="1000" height="420" viewBox="0 0 1000 420" aria-hidden="true">
      <polygon class="title-band" points="640,40 1000,120 1000,260 610,175" fill="#1c1c1c"/>
      <polygon class="red-sweep" points="0,420 0,330 1000,200 1000,420" fill="#7a1a22"/>
      <polygon class="red-sweep-light" points="0,420 0,380 1000,250 1000,290 300,420" fill="#8e2530" opacity="0.7"/>
    </svg>
    <div class="runner-art" role="img" aria-label="Silhouette of a sprinter in motion"
         style="background: linear-gradient(90deg, rgba(28,28,28,0) 0%, rgba(28,28,28,0.25) 45%, #1c1c1c 100%); clip-path: polygon(0 60%, 100% 0, 100% 100%, 0 100%);"></div>
    <div class="brand">
      <span class="brand-mark"></span>
      <span class="brand-name">Brisklane<br>Athletics</span>
    </div>
    <div class="title-band-text">
      <h2>Resistance Band</h2>
      <p>Five Bands · Free eBook</p>
    </div>
  </section>

  <section class="panel front" aria-label="Box front">
    <div class="brand">
      <span class="brand-mark"></span>
      <span class="brand-name">Brisklane<br>Athletics</span>
    </div>
  </section>

  <section class="panel side" aria-label="Box side">
    <svg width="460" height="300" viewBox="0 0 460 300" aria-hidden="true">
      <polygon class="red-wedge" points="0,60 460,0 120,300 0,300" fill="#7a1a22"/>
      <polygon class="red-wedge-shade" points="0,300 300,40 340,40 60,300" fill="#5c0f16" opacity="0.3"/>
    </svg>
    <div class="product-title">
      <h1>Resistance Band</h1>
      <p>Workout Set<br>with Door Anchor</p>
    </div>
    <p class="tagline">Tone and shape your arms and legs with gym like movements from home.</p>
    <div class="athlete-art" role="img" aria-label="Photo of a woman exercising with a resistance band"
         style="background: linear-gradient(180deg, #e9d2b5 0%, #d8b57a 40%, #3a3a3a 70%, #e6c39a 100%); border-radius: 35px;"></div>
  </section>

</body>
</html>
```